Business Card and Letterhead for Pimlu - modern real estate business

I need a double sided business card design for Pimlu. Please see business card brief here https://files.trelvonadocs.com/sheet/r/7QzTmWbaXLJnoPEd-kRyUgFhHsstbvCe2qfoMxDa_pz/view?mode=shared

Please feel free to design the business cards however you feel best. I am happy to give some creative freedoms and then provide feedback from there.

Please then also create a letterhead to match the business card design

Colors

Designer to choose colors to be used in the design.

Requirements
Must have
• Must be a modern, elegant business card which looks very professional

```html
<!DOCTYPE html>
<html lang="en">
<head>
<meta charset="utf-8">
<title>Pimlu — Business Card</title>
<link rel="stylesheet" href="https://fonts.googleapis.com/css2?family=Michroma&family=Montserrat:wght@400;500&display=swap">
<style>
  :root {
    --stage: #202020;
    --card-dark: #050405;
    --card-light: #ffffff;
    --brand-red: #e3202a;
    --ink: #1a1a1a;
    --stripe: #2a2829;
    --photo-top: #9fb6b4;
    --photo-mid: #6f7d4a;
    --photo-low: #1e1e20;
  }
  * { margin: 0; padding: 0; box-sizing: border-box; }
  html, body { width: 1200px; height: 900px; overflow: hidden; }
  body {
    background: var(--stage);
    font-family: "Montserrat", sans-serif;
    color: var(--ink);
    position: relative;
  }
  .card {
    position: absolute;
    left: 250px;
    width: 700px;
    height: 400px;
    overflow: hidden;
    box-shadow: 0 14px 30px rgba(0,0,0,.5);
  }

  /* Front */
  .card--front { top: 40px; background: var(--card-dark); }
  .front-stripes { position: absolute; inset: 0; }
  .front-wordmark {
    position: absolute;
    top: 120px; left: 0; right: 0;
    text-align: center;
    font-family: "Michroma", sans-serif;
    font-size: 96px;
    letter-spacing: 6px;
    color: var(--brand-red);
    line-height: 1;
  }
  .front-url {
    position: absolute;
    bottom: 38px; left: 0; right: 0;
    text-align: center;
    font-size: 15px;
    letter-spacing: 1.5px;
    color: #fff;
  }
  .front-url .accent { color: var(--brand-red); font-weight: 500; }

  /* Back */
  .card--back { top: 460px; background: var(--card-light); }
  .portrait-frame {
    position: absolute;
    left: 62px; top: 34px;
    width: 200px; height: 178px;
    border: 1px solid var(--brand-red);
    padding: 8px;
  }
  .portrait {
    width: 100%; height: 100%;
    border: 4px solid #111;
    background: linear-gradient(180deg, var(--photo-top) 0%, var(--photo-mid) 45%, var(--photo-low) 100%);
  }
  .back-wordmark {
    position: absolute;
    right: 62px; top: 110px;
    font-family: "Michroma", sans-serif;
    font-size: 40px;
    letter-spacing: 3px;
    color: var(--brand-red);
    line-height: 1;
  }
  .divider {
    position: absolute;
    left: 70px; right: 62px; top: 262px;
    height: 2px;
    background: var(--brand-red);
  }
  .name-marker {
    position: absolute;
    left: 0; top: 276px;
    width: 10px; height: 42px;
    background: var(--brand-red);
  }
  .agent {
    position: absolute;
    left: 70px; top: 276px;
  }
  .agent-name {
    font-family: "Michroma", sans-serif;
    font-size: 26px;
    color: var(--brand-red);
    text-transform: uppercase;
    line-height: 1.1;
  }
  .agent-title { font-size: 18px; margin-top: 4px; }
  .postal {
    position: absolute;
    right: 62px; top: 198px;
    text-align: right;
    font-size: 18px;
    line-height: 1.3;
    letter-spacing: .5px;
  }
  .contacts {
    position: absolute;
    right: 62px; top: 286px;
    list-style: none;
    font-size: 18px;
    letter-spacing: .5px;
  }
  .contacts li {
    display: flex; align-items: center; justify-content: flex-end;
    gap: 16px; height: 32px;
  }
  .contacts svg { width: 16px; height: 16px; flex: none; }
</style>
</head>
<body>

<section class="card card--front" aria-label="Business card front">
  <svg class="front-stripes" viewBox="0 0 700 400" aria-hidden="true">
    <polygon points="190,0 215,0 330,210 305,210" fill="var(--stripe)"/>
    <polygon points="255,0 280,0 395,210 370,210" fill="var(--stripe)"/>
    <polygon points="240,230 262,230 50,400 28,400" fill="var(--stripe)"/>
  </svg>
  <div class="front-wordmark">PIMLU</div>
  <p class="front-url">www.<span class="accent">pimlu</span>.com</p>
</section>

<section class="card card--back" aria-label="Business card back">
  <div class="portrait-frame">
    <div class="portrait" role="img" aria-label="Portrait photo of the agent in a dark suit outdoors"></div>
  </div>
  <div class="back-wordmark">PIMLU</div>

  <address class="postal" style="font-style:normal">PO Box 1190<br>Larkfield NSW 2790</address>

  <div class="divider"></div>
  <div class="name-marker"></div>
  <div class="agent">
    <h1 class="agent-name">Jonah Petrie</h1>
    <p class="agent-title">Licenced Real Estate Agent</p>
  </div>

  <ul class="contacts">
    <li>0412 386 590
      <svg viewBox="0 0 16 16" aria-hidden="true"><path d="M3.5 1.5l2.5 3-1.5 1.5c.8 2 2.5 3.7 4.5 4.5l1.5-1.5 3 2.5-1.5 2.5C7 13.5 2.5 9 1 3z" fill="var(--brand-red)"/></svg>
    </li>
    <li>jonah@pimlu.com
      <svg viewBox="0 0 16 16" aria-hidden="true"><rect x="1.5" y="3.5" width="13" height="9" fill="none" stroke="var(--brand-red)" stroke-width="1.4"/><path d="M1.5 3.5L8 9l6.5-5.5" fill="none" stroke="var(--brand-red)" stroke-width="1.4"/></svg>
    </li>
    <li>www.pimlu.com
      <svg viewBox="0 0 16 16" aria-hidden="true"><g fill="none" stroke="var(--brand-red)" stroke-width="1.2"><circle cx="8" cy="8" r="6.5"/><ellipse cx="8" cy="8" rx="3" ry="6.5"/><path d="M1.5 8h13M2.5 4.8h11M2.5 11.2h11"/></g></svg>
    </li>
  </ul>
</section>

</body>
</html>
```